Business Card: RW Office Partners - Your organised problem solver

Business Name: RW Office Partners
Website: www.rwofficepartners.com.au
Email: marisol@rwofficepartners.com.au
Mobile: 61 482 907 236
Facebook: @rwofficepartners
Instrgram: @rwofficepartners

Brading Colours:
HEX
#986474
#ddccd3
#7a8498
#c9d8e4
#000000
#ffffff

Tag Line: Your reliable workload helper

Link to DRAFT website:
https://deskhelpcollective.wixsite.com/rw-office-partners

About Page from the website:
My name is Marisol Wrenfield, and I would love to assist you to become more productive in your day to day and achieve your business and personal goals.
My mission is to give you time, time to work on the important tasks of your business or to be able to spend more time with your family. I will take on the tasks you don’t have time for, don’t know well or simply don’t like to do.
I have an extensive background in Administration, Tender Coordination, Document Control, WHS and Quality Management working primarily in the Construction, Mining and Corporate World.
I am passionate about being organised, having order and making things in your life (and mine) easier! I love to watch something unfold and grow into something amazing! I am known for being the go-to problem solver, the organiser of all things, producing high standards of work even under pressure. I’m also a confident communicator, and I understand that you’re busy running your business.

Target Market(s)

Small to Medium Business who require assistance in their business by a virtual assistant.

Industry/Entity Type

Virtual Assistant

Contact Information for Business Card

Mobile: 61 482 907 236

Font styles to use
Sans Serif

Colors
ffffff

Requirements
Must have
• Branding Colours as outlined.
Contact Details as outlined.
Logo as provided.
Proper contact details - mobile, facebook, instragm, website.
Simple, Elegant, very clean looking.
Should not have
• Note cute with pictures.
Not too girly as still want to market to construction companies.

```html
<!DOCTYPE html>
<html lang="en">
<head>
<meta charset="utf-8">
<title>RW Office Partners – Business Card</title>
<link href="https://fonts.googleapis.com/css2?family=Montserrat:wght@600&family=Arimo:wght@400&display=swap" rel="stylesheet">
<style>
  :root {
    --brand-mauve: #986474;
    --brand-blush: #ddccd3;
    --brand-slate: #7a8498;
    --brand-mist: #c9d8e4;
    --card-black: #1e1e1e;
    --ink-white: #ffffff;
    --backdrop: #e4e1de;
  }
  html, body {
    margin: 0;
    padding: 0;
    width: 1200px;
    height: 900px;
    overflow: hidden;
    background: var(--backdrop);
  }
  .canvas {
    position: relative;
    width: 1200px;
    height: 900px;
  }
  .card {
    position: absolute;
    background: var(--card-black);
    box-shadow: 0 3px 8px rgba(0,0,0,0.35);
    overflow: hidden;
  }
  .card--back { left: 330px; top: 90px; width: 558px; height: 345px; }
  .card--front { left: 330px; top: 470px; width: 560px; height: 343px; }

  .brand-name {
    position: absolute;
    margin: 0;
    font-family: "Montserrat", sans-serif;
    font-weight: 600;
    font-size: 32px;
    letter-spacing: 0.5px;
    white-space: nowrap;
  }
  .card--back .brand-name {
    left: 45px;
    top: 48px;
    color: var(--brand-mauve);
  }
  .card--front .brand-name {
    left: 0;
    right: 0;
    top: 148px;
    text-align: center;
    color: var(--ink-white);
  }

  .contact-list {
    position: absolute;
    left: 162px;
    top: 166px;
    margin: 0;
    padding: 0;
    list-style: none;
    font-family: "Arimo", sans-serif;
    font-size: 16px;
    color: var(--ink-white);
  }
  .contact-item {
    display: flex;
    align-items: center;
    height: 25.5px;
  }
  .contact-item svg { width: 18px; height: 18px; margin-right: 7px; flex: none; }
  .contact-item--web { color: var(--brand-slate); }
  .contact-item--social { height: 30px; }
  .contact-gap { height: 10px; }
  .contact-item--social svg { width: 20px; height: 20px; margin-right: 8px; }

  .tagline {
    position: absolute;
    left: 0;
    right: 0;
    top: 282px;
    margin: 0;
    text-align: center;
    font-family: "Montserrat", sans-serif;
    font-weight: 600;
    font-size: 15.5px;
    color: var(--ink-white);
    white-space: nowrap;
  }
</style>
</head>
<body>
<main class="canvas">
  <section class="card card--back" aria-label="Business card, contact side">
    <h2 class="brand-name">RW Office Partners</h2>
    <ul class="contact-list">
      <li class="contact-item">
        <svg viewBox="0 0 18 18" aria-hidden="true"><rect x="1.5" y="1.5" width="15" height="15" rx="2" fill="none" stroke="var(--brand-mauve)" stroke-width="1.5"/><path d="M6 5l2 2-1 1.3c.6 1.3 1.5 2.2 2.7 2.7L11 10l2 2-1.3 1.4C8.6 13 5 9.4 4.6 6.3z" fill="var(--brand-mauve)"/></svg>
        61 482 907 236
      </li>
      <li class="contact-item">
        <svg viewBox="0 0 18 18" aria-hidden="true"><rect x="1" y="4" width="16" height="11" fill="var(--brand-mauve)"/><path d="M1 4.5l8 6 8-6" fill="none" stroke="var(--card-black)" stroke-width="1.3"/></svg>
        marisol@rwofficepartners.com.au
      </li>
      <li class="contact-item contact-item--web">
        <svg viewBox="0 0 18 18" aria-hidden="true"><g fill="none" stroke="var(--brand-mauve)" stroke-width="1.3"><circle cx="9" cy="9" r="7.5"/><ellipse cx="9" cy="9" rx="3.2" ry="7.5"/><path d="M1.5 9h15M3 5h12M3 13h12"/></g></svg>
        www.rwofficepartners.com.au
      </li>
      <li class="contact-gap" aria-hidden="true"></li>
      <li class="contact-item contact-item--social">
        <svg viewBox="0 0 20 20" aria-hidden="true"><circle cx="10" cy="10" r="9" fill="none" stroke="var(--brand-slate)" stroke-width="1.2"/></svg>
        @rwofficepartners
      </li>
      <li class="contact-item contact-item--social">
        <svg viewBox="0 0 20 20" aria-hidden="true"><circle cx="10" cy="10" r="9" fill="none" stroke="var(--brand-slate)" stroke-width="1.2"/></svg>
        @rwofficepartners
      </li>
    </ul>
  </section>

  <section class="card card--front" aria-label="Business card, brand side">
    <h1 class="brand-name">RW Office Partners</h1>
    <p class="tagline">YOUR RELIABLE WORKLOAD HELPER</p>
  </section>
</main>
</body>
</html>
```